Tolvik Commercial Cleaning is lookong for a new business card design.

A fresh new design that's professional and stylish. We need a serious upgrade to our business cards. I have included pictures of our existing ones. Our clients include professional individuals and business owners. We woupdblike something professional and upbeat. Please have fun and see what you come uo with.

Target Market(s)

Property managers, business owners, facility managers and other similar professionals

Industry/Entity Type

Janitorial

Contact Information for Business Card

Name, cell, office number, email, web address

Font styles to use
Sans Serif

Colors

Designer to choose colors to be used in the design.

Requirements
Must have
• please use the green color in our logo
Nice to have
• Bar code
Should not have
• Address

```html
<!DOCTYPE html>
<html lang="en">
<head>
<meta charset="utf-8">
<title>Tolvik Commercial Cleaning – Business Card</title>
<link rel="stylesheet" href="https://fonts.googleapis.com/css2?family=Comfortaa:wght@700&family=Arimo:ital,wght@0,400;0,700;1,400&display=swap">
<style>
  :root {
    --brand-green: #2ea84a;
    --paper: #f7f7f5;
    --ink-grey: #555a5e;
    --rule-grey: #6b6b6b;
    --stage: #1a1a1a;
    --white: #ffffff;
    --tagline: #e6f5ea;
  }
  html, body {
    margin: 0;
    padding: 0;
    width: 1200px;
    height: 963px;
    overflow: hidden;
    background: var(--stage);
  }
  .sheet {
    position: relative;
    width: 1200px;
    height: 963px;
  }
  .card {
    position: absolute;
    left: 240px;
    width: 720px;
    height: 411px;
    border-radius: 30px;
    box-sizing: border-box;
    overflow: hidden;
  }
  .card--front { top: 50px; background: var(--paper); }
  .card--back  { top: 502px; background: var(--brand-green); }

  /* front */
  .holder-name {
    position: absolute;
    left: 52px;
    top: 56px;
    margin: 0;
    font-family: "Comfortaa", sans-serif;
    font-weight: 700;
    font-size: 34px;
    line-height: 1.2;
    color: var(--brand-green);
    letter-spacing: 0.5px;
  }
  .name-rule {
    position: absolute;
    left: 48px;
    right: 48px;
    top: 112px;
    height: 0;
    border-top: 1.5px solid var(--rule-grey);
  }
  .contact-list {
    position: absolute;
    left: 52px;
    top: 130px;
    margin: 0;
    padding: 0;
    list-style: none;
    font-family: "Arimo", sans-serif;
    font-size: 20px;
    line-height: 1.2;
    color: var(--ink-grey);
  }
  .contact-list li {
    display: flex;
    align-items: center;
    gap: 12px;
    margin-bottom: 10px;
  }
  .contact-icon { width: 18px; height: 18px; flex: none; }
  .wordmark-front {
    position: absolute;
    right: 56px;
    top: 240px;
    margin: 0;
    font-family: "Comfortaa", sans-serif;
    font-weight: 700;
    font-size: 34px;
    line-height: 1.2;
    color: var(--brand-green);
    text-align: right;
  }
  .web-address {
    position: absolute;
    right: 56px;
    bottom: 36px;
    margin: 0;
    font-family: "Arimo", sans-serif;
    font-weight: 700;
    font-size: 22px;
    line-height: 1.2;
    color: var(--ink-grey);
  }
  .web-address .domain { color: var(--brand-green); }

  /* back */
  .wordmark-back {
    position: absolute;
    left: 0;
    right: 0;
    top: 125px;
    margin: 0;
    font-family: "Comfortaa", sans-serif;
    font-weight: 700;
    font-size: 44px;
    line-height: 1.15;
    color: var(--white);
    text-align: center;
  }
  .tagline {
    position: absolute;
    left: 0;
    right: 0;
    top: 258px;
    margin: 0;
    font-family: "Arimo", sans-serif;
    font-style: italic;
    font-size: 24px;
    line-height: 1.2;
    color: var(--tagline);
    text-align: center;
    letter-spacing: 0.5px;
  }
</style>
</head>
<body>
<main class="sheet">
  <section class="card card--front" aria-label="Business card front">
    <h1 class="holder-name">marin hollis</h1>
    <div class="name-rule"></div>
    <ul class="contact-list">
      <li>
        <svg class="contact-icon" viewBox="0 0 24 24" aria-hidden="true">
          <path d="M6.6 10.8a15.1 15.1 0 0 0 6.6 6.6l2.2-2.2a1 1 0 0 1 1-.25 11.4 11.4 0 0 0 3.6.57 1 1 0 0 1 1 1V20a1 1 0 0 1-1 1A17 17 0 0 1 3 4a1 1 0 0 1 1-1h3.5a1 1 0 0 1 1 1c0 1.25.2 2.450.57 3.570a1 1 0 0 1-.25 1z" fill="none" stroke="#2ea84a" stroke-width="2"/>
        </svg>
        (555) 014-2297
      </li>
      <li>
        <svg class="contact-icon" viewBox="0 0 24 24" aria-hidden="true">
          <rect x="2.5" y="5" width="19" height="14" rx="1.5" fill="none" stroke="#2ea84a" stroke-width="2"/>
          <path d="M3 6l9 7 9-7" fill="none" stroke="#2ea84a" stroke-width="2"/>
        </svg>
        marin@tolvikcleaning.com
      </li>
    </ul>
    <p class="wordmark-front">tolvik<br>commercial cleaning</p>
    <p class="web-address">www.<span class="domain">tolvikcleaning</span>.com</p>
  </section>

  <section class="card card--back" aria-label="Business card back">
    <p class="wordmark-back">tolvik<br>commercial cleaning</p>
    <p class="tagline">clean spaces, clear minds</p>
  </section>
</main>
</body>
</html>
```